BrimTaps.com

Hey guys!

We are looking for an innovative 1 page web design for our PPC network website - http://quillpeekshot.example/4k82vmtq7r
We are a PPC social media start up, which works with many social media publishers worldwide.
The design must be clean, flat, trendy, we would like to keep our 1 page design structure, but add your own personal touch-up.

We would like you to make it look like a Million $ company.

Good luck!

Target Market(s)

Big Internet Advertising Companies

Number of Pages Required

1 page

```html
<!DOCTYPE html>
<html lang="en">
<head>
<meta charset="utf-8">
<title>BrimTaps.com — Contact</title>
<link href="https://fonts.googleapis.com/css2?family=Open+Sans:wght@300;400;600;700&display=swap" rel="stylesheet">
<style>
:root{
  --bg-soft:#f4f4f4;
  --ink:#333333;
  --ink-muted:#777777;
  --field-line:#c9c9c9;
  --accent:#3a9ee0;
  --chirp:#5bc0eb;
  --chirplane:#00a0d1;
  --pagebook:#3b5998;
  --shotfolio:#ea4c89;
  --blogstack:#34526f;
  --footer:#3b829c;
  --footer-dark:#2e687c;
  --white:#ffffff;
}
*{box-sizing:border-box;margin:0;padding:0}
html,body{width:1200px;height:1153px;overflow:hidden;background:var(--white)}
body{font-family:"Open Sans",Arial,sans-serif;position:relative}

.contact{position:absolute;left:0;top:0;width:1200px;height:619px;background:var(--bg-soft);text-align:center}
.contact__title{position:absolute;top:80px;width:100%;font-weight:300;font-size:31px;color:var(--ink)}
.contact__intro{position:absolute;top:168px;left:250px;width:700px;font-size:17px;font-weight:400;line-height:28px;color:var(--ink-muted)}
.contact-form{position:absolute;left:330px;top:273px;width:540px;height:207px;border:2px solid var(--field-line);border-radius:20px;overflow:hidden;text-align:left}
.contact-form__field{height:55px;border-bottom:2px solid var(--field-line);padding:16px 15px;font-size:13.5px;color:var(--ink-muted)}
.contact-form__field--message{height:auto;border-bottom:none}
.contact-form__grip{position:absolute;right:3px;bottom:3px}
.send-button{position:absolute;left:527px;top:504px;width:146px;height:39px;border:2px solid var(--accent);border-radius:20px;color:var(--accent);font-size:10.5px;font-weight:700;letter-spacing:1px;line-height:35px;text-align:center}

.follow{position:absolute;left:0;top:619px;width:1200px;height:260px;text-align:center}
.follow__brand{position:absolute;top:88px;width:100%;display:flex;justify-content:center;align-items:center;gap:8px;font-size:22px;font-weight:600;color:var(--chirp)}
.follow__dot{width:12px;height:12px;border-radius:50%;background:var(--chirp)}
.follow__line{position:absolute;top:162px;width:100%;font-size:14px;color:var(--ink-muted)}
.follow__handle{color:var(--ink)}

.social-bar{position:absolute;left:0;top:879px;width:1200px;height:98px;display:flex}
.social-bar__item{flex:1;display:flex;align-items:center;justify-content:center;color:var(--white);font-size:18px;font-weight:600}
.social-bar__item--chirplane{background:var(--chirplane)}
.social-bar__item--pagebook{background:var(--pagebook)}
.social-bar__item--shotfolio{background:var(--shotfolio)}
.social-bar__item--blogstack{background:var(--blogstack)}

.site-footer{position:absolute;left:0;top:977px;width:1200px;height:176px;background:var(--footer);color:var(--white);font-size:14px}
.site-footer__item{position:absolute;top:79px}
.site-footer__email{font-weight:600}
.site-footer__signup{position:absolute;left:900px;top:0;width:300px;height:176px;background:var(--footer-dark);display:flex;align-items:center;justify-content:center;font-size:18px}
</style>
</head>
<body>
<section class="contact">
  <h2 class="contact__title">You've Got Questions, We've Got Answers</h2>
  <p class="contact__intro">Temporibus autem quibusdam et aut officiis debitis aut rerum necessitatibus saepe eveniet ut et voluptates repudiandae sint et molestiae non recusandae.</p>
  <div class="contact-form">
    <div class="contact-form__field">Your Name</div>
    <div class="contact-form__field">Your Email Address</div>
    <div class="contact-form__field contact-form__field--message">Your Message</div>
    <svg class="contact-form__grip" width="10" height="10" viewBox="0 0 10 10"><path d="M9 2L2 9M9 5L5 9M9 8L8 9" stroke="#aaa" stroke-width="1"/></svg>
  </div>
  <div class="send-button">SEND FORM</div>
</section>

<section class="follow">
  <div class="follow__brand"><span class="follow__dot"></span>Chirplane</div>
  <p class="follow__line">Follow us <span class="follow__handle">@brimtaps</span> for more awesome updates</p>
</section>

<nav class="social-bar">
  <div class="social-bar__item social-bar__item--chirplane">Chirplane</div>
  <div class="social-bar__item social-bar__item--pagebook">Pagebook</div>
  <div class="social-bar__item social-bar__item--shotfolio">Shotfolio</div>
  <div class="social-bar__item social-bar__item--blogstack">Blogstack</div>
</nav>

<footer class="site-footer">
  <span class="site-footer__item" style="left:45px">© 2014 Brim Taps Inc.</span>
  <span class="site-footer__item site-footer__email" style="left:243px">help@brimtaps.example</span>
  <span class="site-footer__item" style="left:431px">Terms Of Service</span>
  <span class="site-footer__item" style="left:604px">Privacy Policy</span>
  <div class="site-footer__signup">Sign Up Now! →</div>
</footer>
</body>
</html>
```